Northfield Builders Guild Business card

We are looking for a new business card design with photo included.
Our business is a nonprofit construction contractor membership organization. We offer business education, assist with business setup and licensing, provide safety training, and provide a member directory.
URL: www.builderslinkguild.org
Color code:
CMYK: 0 cyan, 42 magenta, 100 yellow, 0 black for Print.
Hexidecimal: #FF9900
RGB: R 255; G 153; B 0

```html
<!DOCTYPE html>
<html lang="en">
<head>
<meta charset="utf-8">
<title>Northfield Builders Guild – Business Card</title>
<link href="https://fonts.googleapis.com/css2?family=Montserrat:wght@700;800&family=Arimo:wght@400&display=swap" rel="stylesheet">
<style>
  :root {
    --guild-orange: #FF9900;
    --card-black: #050505;
    --backdrop: #2b2b2b;
    --white: #ffffff;
  }
  * { box-sizing: border-box; margin: 0; padding: 0; }
  html, body { width: 1200px; height: 1015px; overflow: hidden; }
  body {
    background: var(--backdrop);
    font-family: "Arimo", Arial, sans-serif;
    position: relative;
  }
  .card {
    position: absolute;
    left: 250px;
    width: 700px;
    height: 400px;
    background: var(--card-black);
    overflow: hidden;
    box-shadow: 0 10px 30px rgba(0,0,0,0.5);
  }
  .card--front { top: 60px; }
  .card--back { top: 555px; }

  /* Front */
  .front-wordmark {
    position: absolute;
    left: 0; right: 0; top: 70px;
    text-align: center;
    font-family: "Montserrat", Arial, sans-serif;
    font-weight: 800;
    color: var(--white);
    line-height: 1;
  }
  .front-wordmark .line-main { display: block; font-size: 64px; letter-spacing: -1px; }
  .front-wordmark .line-sub { display: block; font-size: 26px; letter-spacing: 16px; margin-top: 14px; }
  .service-band {
    position: absolute;
    left: 0; right: 0; bottom: 0;
    height: 130px;
    background: var(--guild-orange);
    padding: 30px 40px;
    display: flex;
    flex-wrap: wrap;
    justify-content: center;
    align-content: center;
    gap: 10px 26px;
  }
  .service {
    font-family: "Montserrat", Arial, sans-serif;
    font-weight: 700;
    font-size: 15px;
    color: var(--card-black);
    display: flex;
    align-items: center;
    gap: 7px;
  }
  .service::before {
    content: "";
    width: 10px; height: 10px;
    border-radius: 50%;
    background: var(--card-black);
  }

  /* Back */
  .holder {
    position: absolute;
    top: 46px; left: 0; right: 0;
    text-align: center;
    font-family: "Montserrat", Arial, sans-serif;
    font-weight: 800;
    line-height: 1.1;
  }
  .holder-name { color: var(--guild-orange); font-size: 30px; }
  .holder-title { color: var(--white); font-size: 18px; }
  .contact-list {
    position: absolute;
    left: 44px; top: 150px;
    list-style: none;
    color: var(--white);
    font-size: 19px;
  }
  .contact-list li { display: flex; align-items: center; gap: 10px; margin-bottom: 5px; }
  .contact-icon { width: 24px; height: 24px; flex: none; }
  .address {
    position: absolute;
    right: 44px; top: 150px;
    text-align: right;
    color: var(--white);
    font-size: 19px;
    line-height: 1.25;
    font-style: normal;
  }
  .website { color: var(--guild-orange); display: block; margin-top: 8px; }
  .logo-band {
    position: absolute;
    left: 0; right: 0; bottom: 0;
    height: 110px;
    background: var(--guild-orange);
    display: flex;
    align-items: center;
    justify-content: center;
    font-family: "Montserrat", Arial, sans-serif;
    font-weight: 800;
    font-size: 40px;
    color: var(--card-black);
    letter-spacing: -0.5px;
  }
</style>
</head>
<body>

<section class="card card--front" aria-label="Business card front">
  <div class="front-wordmark">
    <span class="line-main">NORTHFIELD BUILDERS</span>
    <span class="line-sub">GUILD</span>
  </div>
  <div class="service-band">
    <span class="service">BUSINESS EDUCATION</span>
    <span class="service">ASSIST WITH BUSINESS SETUP AND LICENSING</span>
    <span class="service">PROVIDE SAFETY TRAINING</span>
    <span class="service">PROVIDE A MEMBER DIRECTORY</span>
  </div>
</section>

<section class="card card--back" aria-label="Business card back">
  <div class="holder">
    <div class="holder-name">DANIEL WHITMORE</div>
    <div class="holder-title">MANAGING DIRECTOR</div>
  </div>

  <ul class="contact-list">
    <li>
      <svg class="contact-icon" viewBox="0 0 24 24" aria-hidden="true"><circle cx="12" cy="12" r="12" fill="var(--guild-orange)"/><path d="M8 6.5l2 .3 1 2.6-1.3 1.1a7 7 0 0 0 3.8 3.8l1.1-1.3 2.6 1 .3 2c-.2.8-1 1.3-1.8 1.2A10 10 0 0 1 6.8 8.3C6.7 7.5 7.2 6.7 8 6.5z" fill="var(--white)"/></svg>
      (971) 555-0142
    </li>
    <li>
      <svg class="contact-icon" viewBox="0 0 24 24" aria-hidden="true"><circle cx="12" cy="12" r="12" fill="var(--guild-orange)"/><rect x="8" y="5.5" width="8" height="13" rx="1.5" fill="none" stroke="var(--white)" stroke-width="1.6"/><circle cx="12" cy="16" r="0.9" fill="var(--white)"/></svg>
      800-555-0187
    </li>
    <li>
      <svg class="contact-icon" viewBox="0 0 24 24" aria-hidden="true"><circle cx="12" cy="12" r="12" fill="var(--guild-orange)"/><rect x="8.5" y="5.5" width="7" height="4" fill="var(--white)"/><rect x="6" y="10" width="12" height="6" rx="1" fill="var(--white)"/><rect x="8.5" y="14" width="7" height="4.5" fill="var(--white)" stroke="var(--guild-orange)" stroke-width="1"/></svg>
      503.555.0163
    </li>
    <li>
      <svg class="contact-icon" viewBox="0 0 24 24" aria-hidden="true"><circle cx="12" cy="12" r="12" fill="var(--guild-orange)"/><rect x="6" y="8" width="12" height="8.5" rx="1" fill="var(--white)"/><path d="M6.5 8.5L12 13l5.5-4.5" fill="none" stroke="var(--guild-orange)" stroke-width="1.2"/></svg>
      hello@nbguild.org
    </li>
  </ul>

  <address class="address">
    2400 Millrace Road<br>
    Suite #210, Eastbrook<br>
    OR 97000
    <span class="website">www.builderslinkguild.org</span>
  </address>

  <div class="logo-band">NORTHFIELD BUILDERS GUILD</div>
</section>

</body>
</html>
```